NEW Modern Sleek Business Card for VR Language Startup

Our startup is using VR to lead the next wave of world language education. We need a two-sided business card that introduces the larger organization (Brightloom Language Inc) and our contact info on one side and shows the product, Glimwoorld, on the other side.

Side 1 (contact info)= Brightloom Logo and Contact info (name, title, phone, email)

Side 2 (product)= Glimworld logo, text, and website
Text= Culturally Immersive Language Learning Games
Website= www.glimworld-play.com

Target Market(s)

Education, Technology

Contact Information for Business Card

Contact info will be updated upon approval of the design. For now, put this as a placeholder.

Perry Dunmore
Founder & CEO
pdunmore@quillpost-mail.net
(555)-014-2286

Font styles to use
Other font styles liked:
• Gibson and Century Gothic are the brand fonts

Requirements
Nice to have
• I would love to see cohesion between the design and colors of the two logos. I have attached a few business card designs that I like, so you can get a feel for my preferred style.

```html
<!DOCTYPE html>
<html lang="en">
<head>
<meta charset="utf-8">
<title>Brightloom Language – Business Card</title>
<link rel="stylesheet" href="https://fonts.googleapis.com/css2?family=Montserrat:wght@500;600;700&family=Questrial&display=swap">
<style>
  :root {
    --stage: #646464;
    --paper: #ffffff;
    --ink: #1f1f1f;
    --card-dark: #222222;
    --accent-red: #ea3d5a;
    --accent-orange: #f36c3b;
    --accent-purple: #8a55a8;
    --accent-blue: #4fb4e6;
    --divider: #f3a48e;
    --on-dark: #ffffff;
    --rule-blue: #4c8fb0;
  }
  * { box-sizing: border-box; margin: 0; padding: 0; }
  html, body { width: 1200px; height: 1200px; overflow: hidden; }
  body {
    background: var(--stage);
    font-family: "Questrial", "Century Gothic", sans-serif;
    position: relative;
  }
  .card {
    position: absolute;
    left: 240px;
    width: 720px;
    height: 420px;
    border-radius: 26px;
    overflow: hidden;
  }
  .card--front { top: 142px; background: var(--paper); border-top: 2px solid var(--accent-red); }
  .card--back { top: 638px; background: var(--card-dark); }

  .brand { display: flex; align-items: center; }
  .brand__mark {
    border-radius: 50%;
    background: var(--accent-red);
    flex: none;
  }
  .brand__name {
    font-family: "Montserrat", "Century Gothic", sans-serif;
    font-weight: 600;
    line-height: 1;
    text-transform: uppercase;
  }
  .brand__name span { display: block; }

  .company { position: absolute; left: 54px; top: 174px; }
  .company .brand__mark { width: 84px; height: 84px; }
  .company .brand__name { color: var(--ink); margin-left: 12px; }
  .company__word { font-size: 23px; letter-spacing: 2px; }
  .company__sub { font-size: 15px; letter-spacing: 5.2px; margin-top: 10px; }

  .front__divider {
    position: absolute; left: 358px; top: 156px;
    width: 1.5px; height: 120px; background: var(--divider);
  }
  .contact { position: absolute; left: 383px; top: 148px; }
  .contact__name {
    font-family: "Montserrat", "Century Gothic", sans-serif;
    font-weight: 600; font-size: 22px; letter-spacing: 1px;
    color: var(--accent-red); text-transform: uppercase;
  }
  .contact__title { font-size: 16.5px; color: var(--ink); margin-top: 10px; }
  .contact__list { list-style: none; margin-top: 18px; }
  .contact__item {
    display: flex; align-items: center;
    font-size: 16.5px; color: var(--ink); height: 31px;
  }
  .contact__icon { width: 12px; height: 12px; margin: 0 12px 0 5px; flex: none; }

  .front__band { position: absolute; left: 0; bottom: 0; width: 720px; height: 18px; }

  .product {
    position: absolute; left: 0; right: 0; top: 160px;
    justify-content: center;
  }
  .product .brand__mark { width: 100px; height: 100px; }
  .product .brand__name {
    color: var(--on-dark); margin-left: 22px;
    font-size: 44px; letter-spacing: 3px;
  }

  .back__tagline {
    position: absolute; left: 0; right: 0; top: 320px;
    text-align: center; color: var(--on-dark); font-size: 18px;
  }
  .back__web {
    position: absolute; left: 0; right: 0; top: 364px;
    display: flex; align-items: center; color: var(--on-dark); font-size: 18px;
  }
  .back__rule { height: 1px; flex: 1; }
  .back__rule--left { background: linear-gradient(90deg, var(--accent-red), var(--rule-blue)); }
  .back__rule--right { background: linear-gradient(90deg, var(--rule-blue), var(--accent-red)); }
  .back__url { padding: 0 16px; }
</style>
</head>
<body>
  <section class="card card--front" aria-label="Business card front">
    <div class="brand company">
      <div class="brand__mark"></div>
      <div class="brand__name">
        <span class="company__word">Brightloom</span>
        <span class="company__sub">Language</span>
      </div>
    </div>
    <div class="front__divider"></div>
    <div class="contact">
      <p class="contact__name">Perry Dunmore</p>
      <p class="contact__title">Founder &amp; CEO</p>
      <ul class="contact__list">
        <li class="contact__item">
          <svg class="contact__icon" viewBox="0 0 24 24" aria-hidden="true"><path fill="#ea3d5a" d="M6.6 10.8a15.1 15.1 0 0 0 6.6 6.6l2.2-2.2c.3-.3.7-.4 1-.2 1.1.4 2.3.6 3.6.6.6 0 1 .4 1 1V20c0 .6-.4 1-1 1A17 17 0 0 1 3 4c0-.6.4-1 1-1h3.5c.6 0 1 .4 1 1 0 1.3.2 2.5.6 3.6.1.3 0 .7-.2 1z"/></svg>
          (555)-014-2286
        </li>
        <li class="contact__item">
          <svg class="contact__icon" viewBox="0 0 24 24" aria-hidden="true"><path fill="#ea3d5a" d="M2 5h20v14H2z"/><path fill="none" stroke="#fff" stroke-width="2" d="M3 6l9 7 9-7"/></svg>
          pdunmore@quillpost-mail.net
        </li>
      </ul>
    </div>
    <svg class="front__band" viewBox="0 0 720 18" preserveAspectRatio="none" aria-hidden="true">
      <defs>
        <linearGradient id="bandGradient" x1="0" x2="1" y1="0" y2="0">
          <stop offset="0" stop-color="#4fb4e6"/>
          <stop offset="0.38" stop-color="#8a55a8"/>
          <stop offset="0.72" stop-color="#ea3d5a"/>
          <stop offset="1" stop-color="#f36c3b"/>
        </linearGradient>
      </defs>
      <polygon points="0,0 362,0 352,18 0,18" fill="url(#bandGradient)"/>
      <polygon points="379,0 720,0 720,18 370,18" fill="#222222"/>
    </svg>
  </section>

  <section class="card card--back" aria-label="Business card back">
    <div class="brand product">
      <div class="brand__mark"></div>
      <div class="brand__name">Glimworld</div>
    </div>
    <p class="back__tagline">Culturally Immersive Language Learning Games</p>
    <div class="back__web">
      <span class="back__rule back__rule--left"></span>
      <span class="back__url">www.glimworld-play.com</span>
      <span class="back__rule back__rule--right"></span>
    </div>
  </section>
</body>
</html>
```